I have a transportation trucking company and I’m expanding and hiring drivers

I need a flyer for my social media to let people know I’m hiring and looking for drivers , Please incorporate my company logo and i need to flyer to give some information about the position, I will upload some examples,

I do need it to say We are hiring!
We are looking for CDL- Class A Drivers
2 Years Minimum Driving Experience
Percentage Pay
Clean Driving Record
No Violations or accidents
Weekly Direct Deposit
Sign On bonus
Holiday Bonus
Detention/ Layover Pay
Must Stay out a minimum of 2 full weeks

Interested in more information?
Email info@marlowfreight.com
(318) 596-4021

Harbeck Freight LLC
825 Birchfield Avenue Suite 200 Jenkintown PA 19046

Industry/Entity Type

Long Distance Trucking

Font styles to use
Serif
Sans Serif
Decorative
Script

Requirements
Must have
• Please incorporate my logo into the flyer

Please have just the flyer take up the whole canvas this will be printed and posted on our social media’s
Nice to have

```html
<!DOCTYPE html>
<html lang="en">
<head>
<meta charset="utf-8">
<title>Harbeck Freight LLC – We are hiring</title>
<link rel="stylesheet" href="https://fonts.googleapis.com/css2?family=Dosis:wght@500;600;700&family=Economica:wght@700&display=swap">
<style>
  :root {
    --brand-blue: #2462ad;
    --ink-grey: #5a5a5a;
    --accent-yellow: #e6ea3c;
    --white: #ffffff;
    --sky-top: #8fb6de;
    --sky-bottom: #dce8f2;
  }
  * { margin: 0; padding: 0; box-sizing: border-box; }
  html, body { width: 1164px; height: 1200px; overflow: hidden; background: var(--white); }
  .flyer {
    position: relative;
    width: 1164px;
    height: 1200px;
    overflow: hidden;
    font-family: "Dosis", sans-serif;
  }
  .backdrop { position: absolute; inset: 0; width: 1164px; height: 1200px; }

  .brand-mark {
    position: absolute;
    left: 150px;
    top: 56px;
    width: 104px;
    height: 104px;
    background: var(--brand-blue);
  }
  .brand-name {
    position: absolute;
    left: 26px;
    top: 188px;
    width: 360px;
    font-family: "Dosis", sans-serif;
    font-weight: 700;
    color: var(--brand-blue);
    font-size: 38px;
    line-height: 44px;
    letter-spacing: 1px;
    text-transform: uppercase;
    text-align: center;
  }

  .headline {
    position: absolute;
    left: 0;
    top: 0;
    width: 1164px;
    height: 1200px;
    pointer-events: none;
  }
  .headline-text {
    font-family: "Economica", sans-serif;
    font-weight: 700;
    font-size: 168px;
    fill: var(--brand-blue);
  }

  .section-title {
    position: absolute;
    left: 18px;
    font-weight: 600;
    color: var(--accent-yellow);
    white-space: nowrap;
    line-height: 1;
  }
  .section-title::before { content: "\2605"; font-size: 0.7em; margin-right: 2px; vertical-align: 0.1em; }
  .title-roles { top: 576px; font-size: 47px; }
  .title-contact { top: 1048px; font-size: 50px; }

  .requirements {
    position: absolute;
    left: 40px;
    top: 632px;
    list-style: none;
    color: var(--white);
    font-size: 37px;
    font-weight: 500;
    line-height: 40px;
    white-space: nowrap;
  }
  .requirements li::before { content: "-"; color: #4a8a6a; margin-right: 2px; }

  .contact {
    position: absolute;
    top: 1104px;
    font-size: 42px;
    font-weight: 500;
    color: var(--white);
    line-height: 1;
    white-space: nowrap;
  }
  .contact-email { left: 40px; }
  .contact-phone { left: 657px; }
</style>
</head>
<body>
<main class="flyer">
  <svg class="backdrop" viewBox="0 0 1904 1946" preserveAspectRatio="none">
    <defs>
      <linearGradient id="sky" x1="0" y1="0" x2="0" y2="1">
        <stop offset="0" stop-color="var(--sky-top)"/>
        <stop offset="1" stop-color="var(--sky-bottom)"/>
      </linearGradient>
      <linearGradient id="truck" x1="0" y1="0" x2="0" y2="1">
        <stop offset="0" stop-color="#b9cbdc"/>
        <stop offset="0.45" stop-color="#e59a3a"/>
        <stop offset="0.8" stop-color="#8a7a66"/>
        <stop offset="1" stop-color="#6e6a62"/>
      </linearGradient>
    </defs>

    <rect class="sky-photo" width="1904" height="1946" fill="url(#sky)" role="img" aria-label="Photo of a cloudy blue sky"/>

    <polygon class="corner-panel" points="0,0 650,0 1030,285 0,790" fill="var(--white)"/>
    <polygon class="chevron-band" points="720,0 1115,275 0,848 0,790 1030,285 650,0" fill="var(--brand-blue)"/>
    <polygon class="grey-stripe" points="230,835 430,795 1820,920 1690,945" fill="#9aa6b3" opacity="0.55"/>
    <polyline class="dashed-trim" points="1115,285 290,822 1690,945" fill="none" stroke="var(--white)" stroke-width="5" stroke-dasharray="14 10"/>

    <polygon class="lower-panel" points="0,845 1690,945 965,1585 1904,1900 1904,1946 0,1946" fill="var(--brand-blue)"/>
    <polygon class="truck-photo" points="1690,945 1904,945 1904,1900 965,1585" fill="url(#truck)" role="img" aria-label="Photo of an orange and yellow road train truck on an outback highway"/>
    <polyline class="dashed-trim" points="1690,945 965,1585 1904,1900" fill="none" stroke="var(--white)" stroke-width="6" stroke-dasharray="10 8"/>
    <rect class="bottom-margin" x="0" y="1900" width="1904" height="46" fill="var(--white)"/>

    <g class="search-icon" fill="none" stroke="var(--white)" stroke-width="14">
      <circle cx="1400" cy="262" r="190" fill="rgba(255,255,255,0.25)"/>
      <polygon points="1530,400 1580,350 1745,500 1690,545"/>
      <line x1="1600" y1="440" x2="1648" y2="395"/>
      <line x1="1650" y1="490" x2="1700" y2="445"/>
    </g>
  </svg>

  <span class="brand-mark"></span>
  <p class="brand-name">Harbeck Freight<br>LLC</p>

  <h1>
    <svg class="headline" viewBox="0 0 1164 1200" aria-label="We are hiring!">
      <text class="headline-text" x="545" y="480" textLength="604" lengthAdjust="spacingAndGlyphs">We are hiring!</text>
    </svg>
  </h1>

  <h2 class="section-title title-roles">We are looking for CDL- Class A Drivers</h2>
  <ul class="requirements">
    <li>2 Years Minimum Driving Experience</li>
    <li>Percentage Pay</li>
    <li>Clean Driving Record</li>
    <li>No Violations or accidents</li>
    <li>No Violations or accidents</li>
    <li>Weekly Direct Deposit</li>
    <li>Sign On bonus</li>
    <li>Holiday Bonus</li>
    <li>Detention/ Layover Pay</li>
    <li>Must Stay out a minimum of 2 full week</li>
  </ul>

  <h2 class="section-title title-contact">Interested in more information?</h2>
  <p class="contact contact-email">Email info@marlowfreight.com</p>
  <p class="contact contact-phone">(318) 596-4021</p>
</main>
</body>
</html>
```